Coastline Premier Retreats Business Card Design

Design a business card for Coastline Premier Retreats. Look at the website for colors and reference. Card should have logo, name, title, office number, mobile number, email, URL and a tagline like, "Luxury Hotel & Resort Email Marketing" (This might change).

https://www.coastlinepremierretreats.example

The rest I will leave up to your imagination.

Contact Information for Business Card

Logo, name, title, office number, mobile number, email, URL and a tagline like, "Luxury Hotel & Resort Email Marketing" (This might change).

```html
<!DOCTYPE html>
<html lang="en">
<head>
<meta charset="utf-8">
<title>Coastline Premier Retreats – Business Cards</title>
<link rel="stylesheet" href="https://fonts.googleapis.com/css2?family=Montserrat:ital,wght@0,400;0,500;0,700;0,800;1,500&display=swap">
<style>
  :root {
    --board: #999999;
    --card: #1a1a1a;
    --accent: #ec6e12;
    --ink: #ffffff;
  }
  * { margin: 0; padding: 0; box-sizing: border-box; }
  html, body { width: 1200px; height: 854px; overflow: hidden; }
  body {
    background: var(--board);
    font-family: "Montserrat", sans-serif;
    color: var(--ink);
    position: relative;
  }
  .card {
    position: absolute;
    width: 485px;
    height: 277px;
    background: var(--card);
    border-left: 3px solid var(--accent);
    border-bottom: 3px solid var(--accent);
    box-shadow: 6px 8px 10px rgba(0,0,0,0.25);
  }
  .card--a { left: 96px;  top: 124px; }
  .card--b { left: 620px; top: 124px; }
  .card--c { left: 96px;  top: 439px; }
  .card--back { left: 620px; top: 439px; }

  .brand {
    position: absolute;
    left: 27px;
    top: 52px;
    display: flex;
    align-items: center;
    gap: 8px;
    font-weight: 800;
    font-size: 15px;
    line-height: 1.05;
    letter-spacing: 0.5px;
    text-transform: uppercase;
    color: var(--ink);
  }
  .brand__mark {
    width: 12px; height: 12px;
    background: var(--accent);
    flex: none;
  }

  .person {
    position: absolute;
    right: 24px;
    top: 120px;
    text-align: right;
  }
  .person__name {
    font-weight: 700;
    font-size: 21px;
    letter-spacing: 0.6px;
    color: var(--accent);
    text-transform: uppercase;
    line-height: 1;
  }
  .person__title {
    font-size: 11.5px;
    font-weight: 500;
    letter-spacing: 0.4px;
    margin-top: 3px;
  }
  .person-bar {
    position: absolute;
    right: 0;
    top: 125px;
    width: 13px;
    height: 28px;
    background: var(--accent);
  }

  .contacts {
    position: absolute;
    left: 27px;
    top: 176px;
    list-style: none;
    font-size: 11.2px;
    font-weight: 500;
    letter-spacing: 0.3px;
  }
  .contacts li {
    height: 18.5px;
    display: flex;
    align-items: center;
    gap: 5px;
  }
  .contacts svg { width: 9px; height: 9px; flex: none; fill: var(--accent); }
  .contacts .domain { color: var(--accent); }

  .back-brand {
    position: absolute;
    left: 0; right: 0;
    top: 102px;
    display: flex;
    justify-content: center;
    align-items: center;
    gap: 14px;
    font-weight: 800;
    font-size: 28px;
    letter-spacing: 1px;
    text-transform: uppercase;
  }
  .back-brand .brand__mark { width: 18px; height: 18px; }
  .tagline {
    position: absolute;
    left: 0; right: 0;
    top: 232px;
    text-align: center;
    font-style: italic;
    font-weight: 500;
    font-size: 13.5px;
    color: var(--accent);
  }
</style>
</head>
<body>

<svg width="0" height="0" style="position:absolute">
  <defs>
    <symbol id="icon-mobile" viewBox="0 0 10 10"><path d="M3 0h4a1 1 0 0 1 1 1v8a1 1 0 0 1-1 1H3a1 1 0 0 1-1-1V1a1 1 0 0 1 1-1zm0 1.5v6h4v-6z"/></symbol>
    <symbol id="icon-phone" viewBox="0 0 10 10"><path d="M0 3.5C2 1.5 8 1.5 10 3.5L9 5 7 4.3V3.4C6 3 4 3 3 3.4v.9L1 5z M2.5 5.5h5L9 9H1z"/></symbol>
    <symbol id="icon-mail" viewBox="0 0 10 10"><path d="M0 4l5-3.5L10 4v6H0zm1 .6v4.4h8V4.6L5 7.3z"/></symbol>
    <symbol id="icon-web" viewBox="0 0 10 10"><path d="M5 0a5 5 0 1 1 0 10A5 5 0 0 1 5 0zm-2 2.5 1 2-1 1.5 1 2.5 1-2 1.5-.5-1-2 1.5-1.5L5 1.5z"/></symbol>
  </defs>
</svg>

<section class="card card--a">
  <div class="brand"><span class="brand__mark"></span><span>Coastline<br>Premier Retreats</span></div>
  <div class="person">
    <p class="person__name">Marcus Hale</p>
    <p class="person__title">CEO/Founder</p>
  </div>
  <span class="person-bar"></span>
  <ul class="contacts">
    <li><svg><use href="#icon-mobile"/></svg>555.201.4380</li>
    <li><svg><use href="#icon-phone"/></svg>+34 600 555 214</li>
    <li><svg><use href="#icon-mail"/></svg>marcus@coastlinepremierretreats.example</li>
    <li><svg><use href="#icon-web"/></svg>www.<span class="domain">coastlinepremierretreats</span>.example</li>
  </ul>
</section>

<section class="card card--b">
  <div class="brand"><span class="brand__mark"></span><span>Coastline<br>Premier Retreats</span></div>
  <div class="person">
    <p class="person__name">Selene Varga</p>
    <p class="person__title">CEO/Founder</p>
  </div>
  <span class="person-bar"></span>
  <ul class="contacts">
    <li><svg><use href="#icon-mobile"/></svg>+34 600 555 214</li>
    <li><svg><use href="#icon-phone"/></svg>+100 555 01927</li>
    <li><svg><use href="#icon-mail"/></svg>selene@coastlinepremierretreats.example</li>
    <li><svg><use href="#icon-web"/></svg>www.<span class="domain">coastlinepremierretreats</span>.example</li>
  </ul>
</section>

<section class="card card--c">
  <div class="brand"><span class="brand__mark"></span><span>Coastline<br>Premier Retreats</span></div>
  <div class="person">
    <p class="person__name">Dorian Westbrook</p>
    <p class="person__title">CEO/Founder</p>
  </div>
  <span class="person-bar"></span>
  <ul class="contacts">
    <li><svg><use href="#icon-mobile"/></svg>555.318.9064</li>
    <li><svg><use href="#icon-phone"/></svg>+100 555 01927</li>
    <li><svg><use href="#icon-mail"/></svg>dorian@coastlinepremierretreats.example</li>
    <li><svg><use href="#icon-web"/></svg>www.<span class="domain">coastlinepremierretreats</span>.example</li>
  </ul>
</section>

<section class="card card--back">
  <div class="back-brand"><span class="brand__mark"></span><span>Coastline<br>Premier Retreats</span></div>
  <p class="tagline">Luxury Hotel &amp; Resort Email Marketing</p>
</section>

</body>
</html>
```